Water ATM Card

Need a design for water ATM cards. Size of card is 3.375 x 2.125 inch
On the Front include the Cedar hollow Logo.
Bottom right corner should have Price $100
On the Back
This card is to be used to access water refills at any Cedar Hollow Water Vending Machines.
Please contact (869) 418 2930 or (869) 534 1276 or email clearflowbox@mailvista.example for any assistance or recharging of card.

```html
<!DOCTYPE html>
<html lang="en">
<head>
<meta charset="UTF-8">
<title>Cedar Hollow Water Card</title>
<link href="https://fonts.googleapis.com/css2?family=Montserrat:wght@400;500;700;800&display=swap" rel="stylesheet">
<style>
  :root {
    --page-bg: #9a9a9a;
    --navy: #1f3a8a;
    --navy-deep: #27358a;
    --blue: #1f63b4;
    --blue-light: #2a7cc4;
    --green: #3fa33a;
    --white: #ffffff;
    --off-white: #f1f2f4;
    --text-dark: #1a1a1a;
    --muted-logo: #1d2f78;
  }
  * { box-sizing: border-box; margin: 0; padding: 0; }
  html, body { width: 1200px; height: 900px; overflow: hidden; }
  body {
    background: var(--page-bg);
    font-family: "Montserrat", Arial, sans-serif;
    position: relative;
  }
  .card {
    position: absolute;
    left: 280px;
    width: 640px;
    height: 403px;
    border-radius: 6px;
    overflow: hidden;
    box-shadow: 0 6px 18px rgba(0,0,0,0.25);
  }

  /* Back */
  .card-back { top: 36px; }
  .card-back .back-fill {
    position: absolute; inset: 0;
    background: linear-gradient(160deg, var(--blue-light) 0%, var(--navy-deep) 55%, var(--navy) 100%);
  }
  .card-back .brand-name {
    position: absolute; left: 0; right: 0; top: 110px;
    text-align: center;
    font-weight: 800; font-size: 38px; letter-spacing: 2px;
    color: var(--muted-logo);
    text-transform: uppercase;
  }
  .card-back .usage {
    position: absolute; left: 60px; right: 60px; top: 196px;
    text-align: center;
    font-size: 14px; font-weight: 500; line-height: 1.6;
    color: var(--white);
  }
  .card-back .usage p + p { margin-top: 6px; }

  /* Front */
  .card-front { top: 470px; background: linear-gradient(180deg, var(--white), var(--off-white)); }
  .card-front .wave { position: absolute; inset: 0; }
  .card-front .brand {
    position: absolute; left: 38px; top: 176px;
    display: flex; align-items: center; gap: 10px;
  }
  .card-front .brand-mark {
    width: 16px; height: 16px; border-radius: 50%; background: var(--green);
  }
  .card-front .brand-name {
    font-weight: 800; font-size: 24px; color: var(--blue);
    text-transform: uppercase; letter-spacing: 0.5px;
  }
  .card-front .divider {
    position: absolute; left: 300px; top: 74px; width: 1.5px; height: 140px;
    background: var(--blue);
  }
  .contact { position: absolute; left: 314px; top: 62px; }
  .contact .person {
    font-weight: 800; font-size: 20px; color: var(--navy); text-transform: uppercase;
  }
  .contact .role {
    font-size: 12px; color: var(--text-dark); text-transform: uppercase; margin: 2px 0 10px 6px;
  }
  .contact ul { list-style: none; }
  .contact li {
    display: flex; align-items: center; gap: 8px;
    font-size: 13.5px; color: var(--text-dark); margin-bottom: 5px;
  }
  .contact svg { width: 14px; height: 14px; flex: none; }
  .price {
    position: absolute; right: 30px; bottom: 38px;
    font-weight: 800; font-size: 30px; color: var(--green);
  }
</style>
</head>
<body>

  <section class="card card-back" aria-label="Card back">
    <div class="back-fill" role="img" aria-label="Blue gradient background"></div>
    <div class="brand-name">Cedar Hollow</div>
    <div class="usage">
      <p>This card is to be used to access water refills at any Cedar Hollow Water Vending Machines.</p>
      <p>Please contact (869) 418 2930 or (869) 534 1276 or email clearflowbox@mailvista.example for any assistance or recharging of card.</p>
    </div>
  </section>

  <section class="card card-front" aria-label="Card front">
    <svg class="wave" viewBox="0 0 640 403" preserveAspectRatio="none" aria-hidden="true">
      <defs>
        <linearGradient id="waveBlue" x1="0" y1="1" x2="1" y2="0">
          <stop offset="0" stop-color="#1a4f9e"/>
          <stop offset="1" stop-color="#2a7cc4"/>
        </linearGradient>
      </defs>
      <path d="M0,403 L0,345 Q380,335 640,200 L640,403 Z" fill="url(#waveBlue)"/>
      <path d="M120,333 Q400,318 625,205" fill="none" stroke="#3fa33a" stroke-width="3"/>
    </svg>

    <div class="brand">
      <span class="brand-mark"></span>
      <span class="brand-name">Cedar Hollow</span>
    </div>

    <div class="divider"></div>

    <div class="contact">
      <div class="person">Daniel Reyes</div>
      <div class="role">Ower</div>
      <ul>
        <li>
          <svg viewBox="0 0 16 16"><path d="M4 1l3 3-2 2c1 2 3 4 5 5l2-2 3 3-2 3C7 15 1 9 1 3z" fill="#1f63b4"/></svg>
          (869) 418 2930
        </li>
        <li>
          <svg viewBox="0 0 16 16"><rect x="4" y="1" width="8" height="14" rx="1.5" fill="none" stroke="#1f63b4" stroke-width="1.6"/><circle cx="8" cy="12.5" r="0.9" fill="#1f63b4"/></svg>
          (869) 534 1276
        </li>
        <li>
          <svg viewBox="0 0 16 16"><rect x="1" y="3" width="14" height="10" fill="#1f63b4"/><path d="M1 3l7 6 7-6" fill="none" stroke="#fff" stroke-width="1.3"/></svg>
          clearflowbox@mailvista.example
        </li>
        <li>
          <svg viewBox="0 0 16 16"><circle cx="8" cy="8" r="6.5" fill="none" stroke="#1f63b4" stroke-width="1.6"/><path d="M1.5 8h13M8 1.5c-3 3-3 10 0 13M8 1.5c3 3 3 10 0 13" fill="none" stroke="#1f63b4" stroke-width="1.1"/></svg>
          www.cedarhollowrefill.example
        </li>
      </ul>
    </div>

    <div class="price">Price $100</div>
  </section>

</body>
</html>
```